New Modern Wix Website Design

We are NOT your typical electrical/home improvement contractor, so we need our website updated. We already have a logo for each division.
We provided a neutral logo with a hard hat, a logo for the home improvement, and a logo for the electrical division. (if we can implement all 3 logos will be great but at least the 2 for the divisions must be used.

We looking for a website that a 10-year-old can understand, our target audience is the new young generation that wants innovations in their properties, smart homes, cool smart things/gadgets. So we need a website that is fun, simple, eye-catching. (we don't want to appear TOO serious and boring)
NO GENERIC WEBSITES SO MUST BE VERY CREATIVE!!!

We want to be able to share google reviews, a contact box, business hours, our services, etc...

current website kelvantrio.example

Target Market(s)

Contractors in different trades.

Industry/Entity Type

Construction

Colors
FFC000
F8CF3A
FAE287
FDF2CF
FEFAEE

Requirements
Must have
• Modern upmarket look and feel
Nice to have
• already attached supporting images.
Should not have
• basic typical construction boring and depressing look and feel.

```html
<!DOCTYPE html>
<html lang="en">
<head>
<meta charset="utf-8">
<title>Kelvantrio – Home Improvement &amp; Electrical</title>
<link href="https://fonts.googleapis.com/css2?family=Poppins:wght@400;500;600;700&family=Roboto:ital,wght@0,400;0,500;1,400&display=swap" rel="stylesheet">
<style>
:root{
  --gold:#c8922b;
  --gold-deep:#b6841f;
  --gold-soft:#d9a53e;
  --ink:#1b1b1b;
  --text:#444;
  --muted:#6d6d6d;
  --light:#f3f3f3;
  --line:#dcdcdc;
  --dark:#0e0e0e;
  --white:#fff;
}
*{box-sizing:border-box;margin:0;padding:0}
html,body{width:1200px;height:3976px;overflow:hidden}
body{position:relative;font-family:"Roboto",sans-serif;color:var(--text);background:var(--white)}
.abs{position:absolute}
h1,h2,h3,h4,.brand,.btn{font-family:"Poppins",sans-serif}
.btn{display:inline-flex;align-items:center;justify-content:center;background:var(--gold);color:var(--white);border-radius:30px;font-weight:500;font-size:16px;text-transform:uppercase}

/* header */
.site-header{left:0;top:0;width:1200px;height:111px;background:var(--white)}
.brand{color:var(--ink);font-weight:700;letter-spacing:.5px;display:flex;align-items:center;gap:8px;white-space:nowrap}
.brand .dot{width:14px;height:14px;border-radius:50%;background:var(--gold)}
.header-brand{left:112px;top:40px;font-size:28px}
.contact-chip{display:flex;align-items:center;gap:10px;font-size:16px;color:var(--ink);white-space:nowrap}
.chip-icon{width:34px;height:34px;border-radius:50%;background:var(--gold);display:flex;align-items:center;justify-content:center;flex:none}
.login{left:967px;top:18px;width:120px;height:36px;font-size:16px;text-transform:uppercase}
.main-nav{left:429px;top:75px;display:flex;gap:42px;font-family:"Poppins",sans-serif;font-size:16px;color:var(--ink);font-weight:500}

/* hero */
.hero{left:0;top:111px;width:1200px;height:644px;background:linear-gradient(110deg,#7a5a35 0%,#a27a4c 35%,#8e7055 60%,#4d4c52 100%)}
.hero-title{left:108px;top:318px;font-size:50px;line-height:62px;color:var(--white);font-weight:600}
.hero-text{left:112px;top:391px;width:400px;font-size:17px;line-height:34px;color:var(--white)}
.hero-btn{left:110px;top:484px;width:172px;height:50px}
.hero-dots{left:564px;top:712px;display:flex;gap:12px}
.hero-dots span{width:12px;height:12px;border-radius:50%;background:rgba(255,255,255,.5)}
.hero-dots span.on{background:var(--white)}

/* about */
.about-frame{left:110px;top:834px;width:457px;height:398px;border-left:6px solid var(--gold);border-top:6px solid var(--gold)}
.about-photo{left:120px;top:842px;width:453px;height:390px;background:linear-gradient(135deg,#5c6b7a,#b9c3cc 45%,#3a5a9a 75%,#2b3a55)}
.about-title{left:646px;top:838px;font-size:40px;color:var(--ink);font-weight:600}
.about-body{left:646px;top:905px;width:434px;font-size:14.5px;line-height:33.5px;color:var(--text);text-align:justify}
.about-body p+p{margin-top:12px}
.about-btn{left:646px;top:1174px;width:172px;height:50px}

/* services */
.services{left:0;top:1322px;width:1200px;height:670px;background:var(--light)}
.section-title{width:1200px;left:0;text-align:center;font-size:40px;font-weight:600;color:var(--ink)}
.service-card{top:1459px;width:468px;height:457px;background:var(--white)}
.service-photo{left:0;top:0;width:468px;height:284px}
.badge{left:152px;top:195px;width:164px;height:90px;background:var(--white);border-radius:82px 82px 0 0;display:flex;align-items:flex-end;justify-content:center;padding-bottom:20px}
.badge .brand{font-size:17px}
.service-card h3{position:absolute;left:0;top:314px;width:100%;text-align:center;font-size:26px;font-weight:500;color:var(--ink);text-transform:uppercase}
.service-card p{position:absolute;left:36px;top:356px;width:396px;text-align:center;font-size:14px;line-height:26px;color:var(--text)}

/* testimonials */
.testimonials{left:0;top:1992px;width:1200px;height:499px;background:linear-gradient(160deg,#c8922b,#b7861f 55%,#c28e28);border-top:8px solid var(--gold-soft)}
.testi-title{top:2070px;color:var(--white)}
.quote-ring{left:572px;top:2135px;width:56px;height:56px;border:2px solid var(--white);border-radius:50%;display:flex;align-items:center;justify-content:center}
.testi-quote{left:220px;top:2196px;width:760px;text-align:center;font-style:italic;font-size:16px;line-height:31px;color:var(--white)}
.author{left:450px;top:2314px;display:flex;align-items:center;gap:14px;color:var(--white)}
.avatar{width:54px;height:54px;border-radius:50%;background:#e9d9bf}
.author b{display:block;font-family:"Poppins",sans-serif;font-weight:600;font-size:17px}
.author small{font-size:14px}
.testi-dots{left:572px;top:2416px;display:flex;gap:10px}
.testi-dots span{width:11px;height:11px;border-radius:50%;background:rgba(255,255,255,.5)}
.testi-dots span.on{background:var(--white)}

/* blog */
.blog-card{top:2642px;width:313px;height:406px;border:1px solid var(--line);border-radius:4px;background:var(--white);overflow:hidden}
.blog-photo{width:100%;height:213px}
.blog-card h4{margin:16px 14px 0;font-size:19px;line-height:28px;font-weight:600;color:var(--ink)}
.blog-card p{margin:10px 14px 0;font-size:12.5px;line-height:24px;color:var(--text)}
.read-more{display:block;margin:10px 14px 0;font-size:13px;font-weight:500;color:var(--gold);text-decoration:underline}

/* contact */
.footer{left:0;top:3533px;width:1200px;height:443px;background:var(--dark)}
.contact-box{left:131px;top:3134px;width:944px;height:511px;background:var(--white);border-radius:8px;overflow:hidden;box-shadow:0 4px 18px rgba(0,0,0,.12)}
.contact-side{left:0;top:0;width:439px;height:511px;background:linear-gradient(150deg,#c8922b,#b98825 60%,#c99633)}
.side-brand{left:38px;top:70px;color:var(--white);font-size:30px}
.side-brand .dot{background:var(--white)}
.side-info{left:38px;top:236px;color:var(--white);font-size:17px;line-height:42px;font-family:"Poppins",sans-serif}
.side-info div{display:flex;align-items:center;gap:8px}
.follow{left:38px;top:388px;color:var(--white);font-family:"Poppins",sans-serif;font-weight:500;font-size:17px}
.socials{left:42px;top:422px;display:flex;gap:8px}
.socials span{width:28px;height:28px;border:1.5px solid var(--white);border-radius:50%}
.contact-title{left:480px;top:52px;font-size:38px;font-weight:600;color:var(--ink)}
.contact-sub{left:480px;top:110px;font-size:17px;font-weight:500;color:var(--ink);font-family:"Poppins",sans-serif}
.field{left:481px;width:382px;height:48px;border:1px solid var(--line);display:flex;align-items:flex-start;padding:15px 12px;gap:7px;font-size:14px;color:var(--muted)}
.field.msg{height:102px}
.submit{left:594px;top:432px;width:154px;height:44px;font-size:15px;font-weight:600}

/* footer */
.foot-col{top:3718px;color:var(--white)}
.foot-col h4{font-family:"Poppins",sans-serif;font-size:20px;font-weight:500;margin-bottom:8px}
.foot-col li{list-style:none;font-size:15px;line-height:28px;font-family:"Poppins",sans-serif}
.news-field{left:774px;top:3766px;width:314px;height:48px;border-radius:24px;background:var(--white);padding:14px 24px;font-size:14px;color:var(--ink);font-family:"Poppins",sans-serif}
.news-btn{left:774px;top:3826px;width:314px;height:48px;font-size:16px;font-weight:600}
.foot-rule{left:112px;top:3911px;width:977px;height:1px;background:#333}
.copyright{left:0;top:3928px;width:1200px;text-align:center;color:var(--white);font-size:15px;font-family:"Poppins",sans-serif}
</style>
</head>
<body>

<header class="site-header abs">
  <div class="brand header-brand abs"><span class="dot"></span>KELVANTRIO</div>
  <div class="contact-chip abs" style="left:504px;top:20px">
    <span class="chip-icon"><svg width="16" height="16" viewBox="0 0 24 24"><path fill="#fff" d="M6.6 10.8a15 15 0 0 0 6.6 6.6l2.2-2.2a1 1 0 0 1 1-.25 11.4 11.4 0 0 0 3.6.57 1 1 0 0 1 1 1V20a1 1 0 0 1-1 1A17 17 0 0 1 3 4a1 1 0 0 1 1-1h3.5a1 1 0 0 1 1 1c0 1.25.2 2.45.57 3.57a1 1 0 0 1-.25 1z"/></svg></span>
    +1 (555) 014-2290
  </div>
  <div class="contact-chip abs" style="left:712px;top:20px">
    <span class="chip-icon"><svg width="16" height="16" viewBox="0 0 24 24"><path fill="#fff" d="M3 5h18v14H3z"/><path d="M3 5l9 7 9-7" stroke="#c8922b" stroke-width="2" fill="none"/></svg></span>
    info@kelvantrio.example
  </div>
  <div class="btn login abs">
    <svg width="14" height="14" viewBox="0 0 24 24" style="margin-right:7px"><circle cx="12" cy="7" r="5" fill="#fff"/><path d="M2 23a10 9 0 0 1 20 0z" fill="#fff"/></svg>Login
  </div>
  <nav class="main-nav abs"><span>HOME</span><span>ABOUT</span><span>JOB OPPORTUNITIES</span><span>CONTACT</span><span>ABOUT</span><span>MORE</span></nav>
</header>

<section class="hero abs" role="img" aria-label="Electrician in a yellow hard hat working on a ladder under exposed ceiling framing"></section>
<h1 class="hero-title abs">KELVANTRIO</h1>
<p class="hero-text abs">Lorem ipsum dolor sit amet, consectr adipiscing elit, sed do eiusmod tempor incididunt</p>
<div class="btn hero-btn abs">Get Started</div>
<svg class="abs" style="left:70px;top:410px" width="26" height="46" viewBox="0 0 26 46"><path d="M24 2L3 23l21 21" stroke="#fff" stroke-width="2" fill="none"/></svg>
<svg class="abs" style="left:1104px;top:410px" width="26" height="46" viewBox="0 0 26 46"><path d="M2 2l21 21L2 44" stroke="#fff" stroke-width="2" fill="none"/></svg>
<div class="hero-dots abs"><span></span><span class="on"></span><span></span></div>

<section aria-label="About">
  <div class="about-frame abs"></div>
  <div class="about-photo abs" role="img" aria-label="Electrician in a blue cap taking notes in front of a fuse panel"></div>
  <h2 class="about-title abs">ABOUT KELVANTRIO</h2>
  <div class="about-body abs">
    <p>We founded Kelvantrio out of a pure passion for people. Our goals, our ambitions, our inspirations, all come together to form a truly amazing company that all of us are proud to be a part of.</p>
    <p>Since opening back in 2016, we have become masters at our craft. We go above and beyond your requests to keep you coming back for more. Explore the rest of our site to learn more about what we offer, and get in touch with any questions.</p>
  </div>
  <div class="btn about-btn abs">Learn More</div>
</section>

<section class="services abs"></section>
<h2 class="section-title abs" style="top:1385px">OUR SERVICES</h2>
<article class="service-card abs" style="left:120px">
  <div class="service-photo abs" role="img" aria-label="Worker renovating a bright interior room" style="background:linear-gradient(135deg,#d8d5cf,#a9a49b 55%,#6f6a62)"></div>
  <div class="badge abs"><div class="brand"><span class="dot"></span>KELVANTRIO</div></div>
  <h3>Home Improvement</h3>
  <p>Lorem ipsum dolor sit amet, consectet adipiscing elit, sed do eiusmod tempor incididunt ut labore et doloregna aliqua. Quis ipsum suspendisse ultrices gravida.</p>
</article>
<article class="service-card abs" style="left:611px">
  <div class="service-photo abs" role="img" aria-label="Electrician in a high-visibility vest at a large switchboard" style="background:linear-gradient(135deg,#c86a2a,#5a4a5a 45%,#2a3a6a 80%,#1b2440)"></div>
  <div class="badge abs"><div class="brand"><span class="dot"></span>KELVANTRIO</div></div>
  <h3>Electrical Services</h3>
  <p>The contractors at Kelvantrio understand the importance of adhering to the highest quality standards in every project we take on. Since our founding in 2016, our expertise</p>
</article>

<section class="testimonials abs"></section>
<h2 class="section-title testi-title abs">TESTIMONIALS</h2>
<div class="quote-ring abs"><svg width="24" height="20" viewBox="0 0 24 20"><path fill="#fff" d="M0 12a8 8 0 0 1 8-10v3a5 5 0 0 0-4 5h4v10H0zM13 12a8 8 0 0 1 8-10v3a5 5 0 0 0-4 5h4v10h-8z"/></svg></div>
<svg class="abs" style="left:110px;top:2236px" width="46" height="20" viewBox="0 0 46 20"><path d="M45 10H2M11 1L2 10l9 9" stroke="#fff" stroke-width="2.5" fill="none"/></svg>
<svg class="abs" style="left:1045px;top:2236px" width="46" height="20" viewBox="0 0 46 20"><path d="M1 10h43M35 1l9 9-9 9" stroke="#fff" stroke-width="2.5" fill="none"/></svg>
<p class="testi-quote abs">Sed ut perspiciatis unde omnis iste natus error sit voluptatem accusantium doloremque laudantium, totam rem aperiam, eaque ipsa quae ab illo inventore veritatis et quasi architecto beatae vitae dicta sunt explicabo. Nemo enim ipsam voluptatem quia voluptas sit aspernatur aut odit aut fugit, sed quia consequuntur magni dolores eos qui ratione voluptatem sequi nesciunt.</p>
<div class="author abs"><div class="avatar" role="img" aria-label="Client portrait"></div><div><b>Dana Whitfield</b><small>Northwell Co</small></div></div>
<div class="testi-dots abs"><span></span><span class="on"></span><span></span></div>

<h2 class="section-title abs" style="top:2564px">LATEST BLOG</h2>
<article class="blog-card abs" style="left:113px">
  <div class="blog-photo" role="img" aria-label="Worker cutting trim in a kitchen with wooden cabinets" style="background:linear-gradient(135deg,#8a5a32,#c9a27a 55%,#6a7aa8)"></div>
  <h4>Lorem ipsum dolor sit amet, consectetur adipiscing</h4>
  <p>Sed ut perspiciatis unde omnis iste natus error sit voluptatem accusantium dolorque laudantium, totam rem aperiam, eaque ipsa quae</p>
  <span class="read-more">READ MORE »</span>
</article>
<article class="blog-card abs" style="left:443px">
  <div class="blog-photo" role="img" aria-label="Two technicians working inside an electrical cabinet" style="background:linear-gradient(135deg,#9aa3ab,#4a5668 55%,#2a3450)"></div>
  <h4>Lorem ipsum dolor sit amet, consectetur adipiscing</h4>
  <p>Sed ut perspiciatis unde omnis iste natus error sit voluptatem accusantium dolorque laudantium, totam rem aperiam, eaque ipsa quae</p>
  <span class="read-more">READ MORE »</span>
</article>
<article class="blog-card abs" style="left:773px">
  <div class="blog-photo" role="img" aria-label="Two electricians in hard hats testing a panel outdoors" style="background:linear-gradient(135deg,#b89a6a,#d6b24a 45%,#5a6a3a 80%,#3a4a2a)"></div>
  <h4>Lorem ipsum dolor sit amet, consectetur adipiscing</h4>
  <p>Sed ut perspiciatis unde omnis iste natus error sit voluptatem accusantium dolorque laudantium, totam rem aperiam, eaque ipsa quae</p>
  <span class="read-more">READ MORE »</span>
</article>

<footer class="footer abs"></footer>

<section class="contact-box abs">
  <div class="contact-side abs">
    <div class="brand side-brand abs"><span class="dot"></span>KELVANTRIO</div>
    <div class="side-info abs">
      <div><svg width="14" height="18" viewBox="0 0 14 18"><path fill="#fff" d="M7 0a7 7 0 0 1 7 7c0 5-7 11-7 11S0 12 0 7a7 7 0 0 1 7-7zm0 4a3 3 0 1 0 0 6 3 3 0 0 0 0-6z"/></svg>Fernbrook, PA 10123</div>
      <div><svg width="16" height="16" viewBox="0 0 24 24"><path fill="#fff" d="M6.6 10.8a15 15 0 0 0 6.6 6.6l2.2-2.2a1 1 0 0 1 1-.25 11.4 11.4 0 0 0 3.6.57 1 1 0 0 1 1 1V20a1 1 0 0 1-1 1A17 17 0 0 1 3 4a1 1 0 0 1 1-1h3.5a1 1 0 0 1 1 1c0 1.25.2 2.45.57 3.57a1 1 0 0 1-.25 1z"/></svg>+1 (555) 014-2290</div>
      <div><svg width="16" height="12" viewBox="0 0 16 12"><rect width="16" height="12" fill="#fff"/><path d="M0 0l8 6 8-6" stroke="#c8922b" fill="none"/></svg>info@kelvantrio.example</div>
    </div>
    <div class="follow abs">Follow Us On</div>
    <div class="socials abs"><span></span><span></span><span></span></div>
  </div>
  <h2 class="contact-title abs">CONTACT US</h2>
  <div class="contact-sub abs">Please describe your project or specific needs</div>
  <div class="field abs" style="top:188px">Name</div>
  <div class="field abs" style="top:244px">Email Address</div>
  <div class="field abs" style="top:300px">Contact No</div>
  <div class="field msg abs" style="top:355px">Message</div>
  <div class="btn submit abs">Submit</div>
</section>

<div class="foot-col abs" style="left:113px"><h4>business hours</h4><ul><li>Mon - Fri</li><li>8 a.m. to 5 p.m.</li><li>Sat - sun</li><li>8 a.m. to 1p.m.</li></ul></div>
<div class="foot-col abs" style="left:343px"><h4>Company</h4><ul><li>Home</li><li>About</li><li>Job Opportunities</li><li>Contact</li><li>About</li></ul></div>
<div class="foot-col abs" style="left:543px"><h4>Services</h4><ul><li>Home Improvement</li><li>Electrical Services</li></ul></div>
<div class="foot-col abs" style="left:776px"><h4>Subscribe to our Newsletter</h4></div>
<div class="news-field abs">Email Address</div>
<div class="btn news-btn abs">Subscribe</div>
<div class="foot-rule abs"></div>
<div class="copyright abs">© 2021 Kelvantrio. All Rights Reserved.</div>

</body>
</html>
```